Vantro cards

I am in the auto motive, transportation business I would like a business card that is Something cool, modern edgy, having to do with car culture. I offer towing service for high and exotic cars. I also provide towing for collisions and car accidents. I offer open and enclosed transport nationwide.

Target Market(s)

Car culture people high end auto collectors

Industry/Entity Type

Towing car carrier

Contact Information for Business Card

My company colors black yellow and silver

Font styles to use
Serif

```html
<!DOCTYPE html>
<html lang="en">
<head>
<meta charset="utf-8">
<title>Vantro Business Card</title>
<link href="https://fonts.googleapis.com/css2?family=Montserrat:wght@400;600;700;800&display=swap" rel="stylesheet">
<style>
  :root {
    --yellow: #f9dc5c;
    --black: #111111;
    --charcoal: #222222;
    --silver: #d9d9d9;
    --navy: #1f2340;
    --white: #ffffff;
    --backdrop: #e7e4df;
  }
  * { box-sizing: border-box; margin: 0; padding: 0; }
  html, body { width: 900px; height: 1200px; overflow: hidden; }
  body {
    background: var(--backdrop);
    font-family: "Montserrat", Arial, sans-serif;
    position: relative;
  }
  .card {
    position: absolute;
    left: 80px;
    width: 742px;
    height: 442px;
    border-radius: 30px;
    overflow: hidden;
  }
  .card-front { top: 132px; background: var(--white); }
  .card-back { top: 638px; background: var(--charcoal); }

  .vehicle-art {
    position: absolute;
    border-radius: 60px 20px 0 0;
  }
  .card-front .vehicle-art {
    left: 340px; top: 40px; width: 402px; height: 380px;
    background: linear-gradient(160deg, rgba(0,0,0,0.03), rgba(0,0,0,0.09));
  }
  .card-back .vehicle-art {
    left: 380px; top: 50px; width: 362px; height: 370px;
    background: linear-gradient(90deg, rgba(10,10,10,0.9), rgba(120,120,120,0.55));
  }

  .brand {
    position: absolute;
    display: flex;
    align-items: center;
    gap: 12px;
    font-weight: 800;
    letter-spacing: 1px;
  }
  .brand-mark { width: 22px; height: 22px; background: var(--yellow); }
  .card-front .brand { left: 36px; top: 110px; font-size: 44px; color: var(--black); }
  .card-back .brand {
    left: 0; right: 0; top: 180px; justify-content: center;
    font-size: 64px; color: var(--white);
  }
  .card-back .brand-mark { width: 30px; height: 30px; }

  .person { position: absolute; left: 35px; top: 256px; }
  .person-name { font-size: 26px; font-weight: 700; color: var(--yellow); line-height: 1.1; }
  .person-role { font-size: 17px; color: var(--navy); margin-top: 2px; }

  .divider {
    position: absolute; left: 33px; top: 314px;
    width: 677px; height: 2px; background: var(--black);
  }

  .contact-list { position: absolute; left: 33px; top: 326px; list-style: none; }
  .contact-list li {
    display: flex; align-items: center; gap: 10px;
    font-size: 16px; color: var(--charcoal); height: 21px;
  }
  .contact-list svg { width: 15px; height: 13px; fill: var(--charcoal); }

  .address {
    position: absolute; left: 530px; top: 348px;
    font-size: 16px; color: var(--charcoal); line-height: 21px; font-style: normal;
  }

  .front-footer { position: absolute; left: 0; bottom: 0; width: 742px; height: 40px; }

  .back-stripe {
    position: absolute; left: 0; bottom: 0; width: 742px; height: 12px;
    background: var(--yellow);
  }
</style>
</head>
<body>

<section class="card card-front">
  <div class="vehicle-art" role="img" aria-label="Faint silhouette of a flatbed tow truck"></div>

  <div class="brand"><span class="brand-mark"></span>VANTRO</div>

  <div class="person">
    <p class="person-name">Dara Kessler</p>
    <p class="person-role">Owner</p>
  </div>

  <div class="divider"></div>

  <ul class="contact-list">
    <li>
      <svg viewBox="0 0 16 14"><path d="M1 4c2-3 12-3 14 0l-2 2-2-1V3H5v2L3 6zM3 7h10l1 6H2z"/></svg>
      (555) 214-7390
    </li>
    <li>
      <svg viewBox="0 0 16 14"><path d="M1 2h14v1L8 8 1 3zM1 5l7 5 7-5v7H1z"/></svg>
      info@vantrotransport.com
    </li>
    <li>
      <svg viewBox="0 0 16 16"><circle cx="8" cy="8" r="7"/></svg>
      www.vantrotransport.com
    </li>
  </ul>

  <address class="address">48 Orchard Lane<br>Fairview, OH 44000</address>

  <svg class="front-footer" viewBox="0 0 742 40" preserveAspectRatio="none">
    <rect x="0" y="11" width="440" height="8" fill="var(--yellow)"/>
    <path d="M0 19 H420 Q445 19 458 8 Q468 0 490 0 H742 V40 H0 Z" fill="var(--black)"/>
    <path d="M0 19 H420 Q445 19 458 8 Q468 0 490 0 H742 V6 H495 Q476 6 466 14 Q450 26 425 26 H0 Z" fill="var(--white)"/>
  </svg>
</section>

<section class="card card-back">
  <div class="vehicle-art" role="img" aria-label="Dark silhouette of a flatbed tow truck"></div>
  <div class="brand"><span class="brand-mark"></span>VANTRO</div>
  <div class="back-stripe"></div>
</section>

</body>
</html>
```